Aquatic View

We need a web design for a new window cleaning company name Tidewell Glass Care. We are located in Grand Cayman, Cayman Islands. We are a small company, a team of husband and wife. Our services include residencial interior and exterior window cleaning and commercial. Extra services such as ceiling fans cleaning, mirrors, high dusting. Home cleaning services. Power washing. Explaining the service. We want a modern, beachy style with aquatic colors. We want to use our domain name "tidewellglasscare.ky". We want to portray a clean, modern and professional design.

Target Market(s)

Big Home owners

Industry/Entity Type

Cleaning Service

Contact Information for Business Card

Company Name: Tidewell Glass Care
Name: Desmond Farrowby owner/manager
Phone: 345-9170452
Email: desmond@tidewellglasscare.ky
Website: tidewellglasscare.ky
Address: P.O.Box 2486 GT, George Town, Grand Cayman KY1-1203 Cayman Islands

Number of Pages Required

2 page

Font styles to use
Sans Serif

Colors
0592cd
0455a3
33a6d7
85cae6
cadf82
abd036
fbf289

Requirements
Nice to have
• Pictures of an ocean view and palm trees from clear windows.
• https://quorvantel.com/bidlinker/
• Use the above for "free estimate".

```html
<!DOCTYPE html>
<html lang="en">
<head>
<meta charset="utf-8">
<title>Tidewell Glass Care</title>
<link href="https://fonts.googleapis.com/css2?family=Lato:ital,wght@0,400;0,700;0,900;1,400&display=swap" rel="stylesheet">
<style>
:root{
  --ink:#333333;
  --text:#5a5a5a;
  --blue:#0592cd;
  --blue-dark:#0455a3;
  --red:#c0141b;
  --topbar:#333333;
  --footer:#2b2b2b;
  --line:#dddddd;
  --white:#ffffff;
}
*{box-sizing:border-box;margin:0;padding:0}
html,body{width:1200px;height:1001px;overflow:hidden;background:#fff;font-family:'Lato',sans-serif;color:var(--text)}
.page{position:relative;width:1200px;height:1001px}
.topbar{position:absolute;left:0;top:0;width:1200px;height:36px;background:var(--topbar)}
.topbar .phone{position:absolute;right:116px;top:5px;display:flex;align-items:center;gap:6px;color:#fff;font-size:20px;font-weight:700}
.header{position:absolute;top:36px;left:0;width:1200px;height:67px;background:#fff}
.brand{position:absolute;left:118px;top:-28px;width:150px;height:95px;display:flex;flex-direction:column;align-items:center;justify-content:flex-end;padding-bottom:10px}
.brand .mark{position:absolute;top:0;left:22px;width:106px;height:106px;border-radius:50%;background:#fff;z-index:0}
.brand .name{position:relative;z-index:1;font-size:17px;font-weight:900;color:var(--ink);text-align:center;line-height:1.05}
.nav{position:absolute;right:116px;top:26px;display:flex;align-items:center;font-size:13.5px;font-weight:700;color:var(--ink)}
.nav a{color:inherit;text-decoration:none;padding:2px 12px;border-left:1px solid #ccc}
.nav a:first-child{border-left:none}
.nav a.active{color:var(--blue);border:1px solid var(--blue);margin-right:6px;padding:2px 13px}
.nav a.gap{padding:0 22px 0 14px}
.hero{position:absolute;top:103px;left:0;width:1200px;height:404px;background:linear-gradient(100deg,#eeeeee 0%,#e4e2df 35%,#cfcac4 60%,#dcdad6 85%,#ececec 100%)}
.hero-title{position:absolute;left:117px;top:150px;font-size:26px;font-weight:900;letter-spacing:.5px;color:var(--ink);line-height:42px}
.arrow-btn{position:absolute;top:194px;width:40px;height:40px;border-radius:50%;background:#f2f2f2;border:2px solid #d6d6d6;display:flex;align-items:center;justify-content:center}
.arrow-btn.prev{left:31px}.arrow-btn.next{right:31px}
.band{position:absolute;top:507px;left:0;width:1200px;height:348px;background:linear-gradient(#dedede,#f6f6f6 40%,#fff)}
.panel{position:absolute;top:506px;left:99px;width:1002px;height:349px;background:#fff}
.col{position:absolute;top:24px}
.col-about{left:17px;width:265px}
.col-services{left:334px;width:334px}
.col-inquiry{left:718px;width:265px}
.divider{position:absolute;top:36px;width:1px;height:270px;background:#eeeeee}
h2{font-size:17px;font-weight:900;letter-spacing:.5px;color:var(--red);padding-bottom:10px;border-bottom:1px solid var(--line);position:relative}
h2 span{color:var(--blue)}
h2::after{content:"";position:absolute;left:0;bottom:-1px;width:86px;height:3px;background:var(--blue-dark)}
.photo{margin-top:14px;width:265px;height:122px;border:1px solid #bbb;background:linear-gradient(120deg,#c7d8e8,#8fb0cc 45%,#4e6f9a 70%,#c9ccc9)}
p{font-size:13px;line-height:17px}
.col-about p{margin-top:10px;line-height:19.5px}
.btn{display:inline-block;background:linear-gradient(#0a7dc7,var(--blue-dark));color:#fff;font-size:13.5px;font-weight:700;padding:7px 9px}
.col-about .btn{margin-top:8px}
.services-intro{margin-top:12px}
.service{margin-top:6px}
.service h3{display:flex;align-items:center;gap:6px;font-size:15px;font-weight:700;color:var(--blue);height:20px}
.service.extra{margin-top:10px}
.inquiry-arrows{position:absolute;right:0;top:2px;font-size:14px;color:#333;letter-spacing:6px}
.field{margin-top:8px;height:30px;border:1px solid #ccc;font-size:12.5px;color:#666;padding:6px}
.field.first{margin-top:16px}
.field.msg{height:73px}
.col-inquiry .btn{margin-top:9px;padding:8px 19px}
.footer{position:absolute;top:855px;left:0;width:1200px;height:107px;background:var(--footer);color:#fff}
.foot-nav{position:absolute;left:117px;top:20px;font-size:13px;font-weight:700;display:flex;gap:0}
.foot-nav span{padding:0 9px}
.foot-nav span:first-child{padding-left:0}
.foot-info{position:absolute;left:116px;font-size:13px;display:flex;align-items:center;gap:6px}
.subscribe{position:absolute;right:116px;top:19px;display:flex;height:30px}
.subscribe .input{width:158px;background:#fff;border-radius:3px 0 0 3px;font-size:11px;font-style:italic;color:#888;display:flex;align-items:center;gap:6px;padding-left:8px}
.subscribe .go{width:84px;background:var(--blue);font-size:12.5px;font-weight:700;display:flex;align-items:center;justify-content:center}
.social{position:absolute;right:116px;top:68px;display:flex;gap:6px}
.social span{width:24px;height:24px;border:1.5px solid #fff;border-radius:50%}
.copyright{position:absolute;top:962px;left:0;width:1200px;height:39px;background:linear-gradient(#1a8fd6,#0a6db8);color:#fff;font-size:13px;display:flex;align-items:center;justify-content:center}
</style>
</head>
<body>
<div class="page">
  <div class="topbar">
    <div class="phone">
      <svg width="26" height="26" viewBox="0 0 26 26"><circle cx="13" cy="13" r="12" fill="none" stroke="#fff" stroke-width="1.5"/><path d="M9 7c1 0 2 2.5 2 3s-1 1-1 1.5 2 3.5 3.5 4c.5 0 1-1 1.5-1s3 1 3 2-1.5 2-2.5 2C11 18.5 7.5 13 7.5 9c0-1 .7-2 1.5-2z" fill="#fff"/></svg>
      345-917-0452
    </div>
  </div>
  <header class="header">
    <div class="brand"><span class="mark"></span><span class="name">TIDEWELL<br>GLASS CARE</span></div>
    <nav class="nav">
      <a class="active">HOME</a><a>ABOUT US</a><a class="gap">SERIVCES</a><a>CONTACT US</a>
    </nav>
  </header>
  <section class="hero" role="img" aria-label="Photo of a smiling couple cleaning a bright modern kitchen">
    <h1 class="hero-title">WE ARE RESIDENTIAL<br>COMMERCIAL<br>CLEANING SERVICE<br>FIRM</h1>
    <div class="arrow-btn prev"><svg width="12" height="14"><path d="M9 1 3 7l6 6" stroke="#555" stroke-width="3" fill="none"/></svg></div>
    <div class="arrow-btn next"><svg width="12" height="14"><path d="m3 1 6 6-6 6" stroke="#555" stroke-width="3" fill="none"/></svg></div>
  </section>
  <div class="band"></div>
  <main class="panel">
    <section class="col col-about">
      <h2>ABOUT <span>TIDEWELL GLASS CARE</span></h2>
      <div class="photo" role="img" aria-label="Photo of a cleaner squeegeeing a tall window"></div>
      <p>Lorem ipsum dolor sit amet, consectetuer adip iscing elit, sed diam nonummy nibh euismod magna aliquam erat volutpat.</p>
      <a class="btn">READ MORE</a>
    </section>
    <div class="divider" style="left:308px"></div>
    <section class="col col-services">
      <h2>OUR <span>SERVICES</span></h2>
      <p class="services-intro">Lorem ipsum dolor sit amet, consectetuer adip iscing elit sed diam nonummy nibh euismod magna.</p>
      <div class="service">
        <h3><svg width="20" height="18" viewBox="0 0 20 18"><path d="M10 1 1 9h3v8h12V9h3z" fill="#555"/><rect x="8" y="11" width="4" height="6" fill="#fff"/></svg>Residential</h3>
        <p>Lorem ipsum dolor sit amet, consectetuer adip iscing elit sed diam nonummy nibh euismod magna.</p>
      </div>
      <div class="service">
        <h3><svg width="20" height="18" viewBox="0 0 20 18"><rect x="2" y="5" width="7" height="13" fill="#555"/><rect x="9" y="1" width="9" height="17" fill="#555"/><path d="M11 4h2v2h-2zm3 0h2v2h-2zm-3 4h2v2h-2zm3 0h2v2h-2zM4 8h2v2H4z" fill="#fff"/></svg>Commercial</h3>
        <p>Lorem ipsum dolor sit amet, consectetuer adip iscing elit sed diam nonummy nibh euismod magna.</p>
      </div>
      <div class="service extra">
        <h3><svg width="20" height="18" viewBox="0 0 20 18"><circle cx="7" cy="7" r="5" fill="none" stroke="#555" stroke-width="3" stroke-dasharray="2 1.5"/><circle cx="15" cy="13" r="3" fill="none" stroke="#555" stroke-width="2.5" stroke-dasharray="1.5 1"/></svg>Extra Services</h3>
        <p>Lorem ipsum dolor sit amet, consectetuer adip iscing elit sed diam nonummy nibh euismod magna.</p>
      </div>
    </section>
    <div class="divider" style="left:693px"></div>
    <section class="col col-inquiry">
      <h2>QUICK <span>INQUIRY</span></h2>
      <span class="inquiry-arrows">‹›</span>
      <div class="field first">Email</div>
      <div class="field">Phone</div>
      <div class="field">Email</div>
      <div class="field msg">Message</div>
      <a class="btn">SUBMIT</a>
    </section>
  </main>
  <footer class="footer">
    <div class="foot-nav"><span>Home</span><span>I</span><span>About Us</span><span>I</span><span>Serivces</span><span>I</span><span>Contact Us</span></div>
    <div class="foot-info" style="top:51px"><svg width="14" height="16" viewBox="0 0 14 16"><path d="M7 1a5 5 0 0 0-5 5c0 4 5 9 5 9s5-5 5-9a5 5 0 0 0-5-5z" fill="#bbb"/><circle cx="7" cy="6" r="2" fill="#2b2b2b"/></svg>P.O.Box 2486 GT, George Town, Grand Cayman KY1-1203</div>
    <div class="foot-info" style="top:75px">
      <svg width="18" height="18" viewBox="0 0 18 18"><circle cx="9" cy="9" r="8" fill="none" stroke="#bbb"/><path d="M6.5 5c.7 0 1.3 1.7 1.3 2s-.6.6-.6 1 1.3 2.3 2.3 2.6c.3 0 .6-.6 1-.6s2 .6 2 1.3-1 1.3-1.6 1.3C8 12.6 5.4 9 5.4 6.3c0-.6.5-1.3 1.1-1.3z" fill="#bbb"/></svg>
      345-917-0453&nbsp;&nbsp;&nbsp;
      <svg width="12" height="9" viewBox="0 0 12 9"><rect width="12" height="9" fill="#bbb"/><path d="m0 0 6 5 6-5" stroke="#2b2b2b" fill="none"/></svg>
      info@tidewellglasscare.ky
    </div>
    <div class="subscribe">
      <div class="input"><svg width="14" height="10" viewBox="0 0 14 10"><rect width="14" height="10" fill="#ddd"/><path d="m0 0 7 5 7-5" stroke="#fff" fill="none"/></svg>your e-mail address</div>
      <div class="go">SUBSCRIBE</div>
    </div>
    <div class="social"><span></span><span></span><span></span><span></span></div>
  </footer>
  <div class="copyright">Copyright © 2015&nbsp; TidewellGlassCare. All Right Reserved</div>
</div>
</body>
</html>
```